Business cards - BRENT Roofing & Siding

We need simple business cards made up for our Roofing & Siding business based in Calgary Alberta.
The logo on one side of the card and potentially our slogan "Built with trust, verified by time".
The other side could have:
-A small logo
-Rep name:
-Rep cell phone:
-Rep email:
-Office phone: 403-684-2093
-Website: PrairieShingleWorks.com

We would like to incorporate the colours from our logo, especially the lite blue on the jpeg file. I have attached the ai file and jpeg file. We like the colours better on the jpeg file.

I do not require a money back guarantee

```html
<!DOCTYPE html>
<html lang="en">
<head>
<meta charset="utf-8">
<title>BRENT Roofing &amp; Siding – Business Cards</title>
<link rel="stylesheet" href="https://fonts.googleapis.com/css2?family=Arimo:wght@400;700&display=swap">
<style>
  :root {
    --backdrop: #2b2d31;
    --card-white: #ffffff;
    --brand-blue: #3b7bcc;
    --brand-blue-deep: #2f68b4;
    --brand-red: #e3262b;
    --ink: #1d1d1f;
    --ink-soft: #333338;
  }
  * { box-sizing: border-box; margin: 0; padding: 0; }
  html, body {
    width: 1200px; height: 900px; overflow: hidden;
    background: var(--backdrop);
    font-family: "Arimo", Arial, sans-serif;
  }
  .canvas {
    position: relative; width: 1200px; height: 900px;
    display: flex; align-items: center; justify-content: center; gap: 40px;
  }
  .card {
    position: relative; width: 540px; height: 308px;
    overflow: hidden; box-shadow: 0 10px 30px rgba(0,0,0,.45);
  }

  /* Front: contact side */
  .card-front { background: var(--card-white); }
  .front-swoosh { position: absolute; inset: 0; width: 100%; height: 100%; }
  .front-brand {
    position: absolute; left: 44px; top: 52px;
    display: flex; align-items: center; gap: 10px;
  }
  .brand-square { width: 16px; height: 16px; background: var(--brand-blue); }
  .front-brand .brand-name {
    font-weight: 700; font-size: 21px; color: var(--ink); letter-spacing: .5px;
  }
  .front-est {
    position: absolute; left: 70px; top: 80px;
    font-size: 11px; color: var(--ink-soft); letter-spacing: 1px;
  }
  .rep {
    position: absolute; left: 262px; top: 118px; width: 260px;
  }
  .rep-accent {
    position: absolute; left: -16px; top: 2px; width: 4px; height: 30px;
    background: var(--brand-blue);
  }
  .rep-name { font-weight: 700; font-size: 24px; color: var(--brand-blue); line-height: 1.1; }
  .rep-title { font-size: 12px; color: var(--ink); margin-top: 3px; }
  .rep-divider {
    position: absolute; left: -70px; top: 56px; width: 70px; height: 2px;
    background: var(--brand-red);
  }
  .rep-address { font-size: 12px; color: var(--ink); margin-top: 16px; line-height: 1.35; }
  .contact-list { list-style: none; margin-top: 10px; font-size: 12px; color: var(--ink); }
  .contact-list li { display: flex; align-items: center; gap: 6px; line-height: 1.45; }
  .contact-icon { width: 10px; height: 10px; flex: none; }

  /* Back: brand side */
  .card-back {
    background: linear-gradient(135deg, #4a8ad6 0%, var(--brand-blue) 50%, var(--brand-blue-deep) 100%);
    display: flex; flex-direction: column; align-items: center; justify-content: center; gap: 10px;
  }
  .back-brand { display: flex; align-items: center; gap: 12px; }
  .back-brand .brand-square { width: 22px; height: 22px; background: var(--card-white); }
  .back-brand .brand-name {
    font-weight: 700; font-size: 32px; color: var(--card-white); letter-spacing: 1px;
  }
  .back-est { font-size: 13px; color: var(--card-white); letter-spacing: 2px; }
</style>
</head>
<body>
<main class="canvas">

  <section class="card card-front" aria-label="Business card, contact side">
    <svg class="front-swoosh" viewBox="0 0 540 308" aria-hidden="true">
      <path d="M0 70 C 60 150, 150 260, 360 308 L 0 308 Z" fill="#3b7bcc"/>
      <path d="M0 58 C 60 145, 150 255, 360 304" fill="none" stroke="#ffffff" stroke-width="8"/>
      <path d="M0 52 C 62 140, 155 250, 345 300" fill="none" stroke="#e3262b" stroke-width="3"/>
    </svg>
    <div class="front-brand">
      <span class="brand-square"></span>
      <span class="brand-name">BRENT Roofing &amp; Siding</span>
    </div>
    <div class="front-est">Est. 1991</div>

    <div class="rep">
      <span class="rep-accent"></span>
      <h1 class="rep-name">Daniel Morrow</h1>
      <p class="rep-title">President and CEO</p>
      <span class="rep-divider"></span>
      <p class="rep-address">2874 - 11 Avenue N.E. Calgary<br>Alberta T2A 4K7</p>
      <ul class="contact-list">
        <li>
          <svg class="contact-icon" viewBox="0 0 10 10" aria-hidden="true"><path d="M2 0.5 L4 2.8 L3 4 Q4.5 6 6 7 L7.2 6 L9.5 8 L8 9.5 Q3.5 9 0.5 2 Z" fill="#e3262b"/></svg>
          403-684-2093
        </li>
        <li>
          <svg class="contact-icon" viewBox="0 0 10 10" aria-hidden="true"><rect x="0.5" y="2" width="9" height="6.5" fill="#e3262b"/><path d="M0.5 2 L5 5.5 L9.5 2" fill="none" stroke="#fff" stroke-width="1"/></svg>
          info@prairieshingleworks.com
        </li>
        <li>
          <svg class="contact-icon" viewBox="0 0 10 10" aria-hidden="true"><circle cx="5" cy="5" r="4.3" fill="none" stroke="#e3262b" stroke-width="1.2"/><path d="M0.7 5 H9.3 M5 0.7 Q2 5 5 9.3 M5 0.7 Q8 5 5 9.3" fill="none" stroke="#e3262b" stroke-width="0.9"/></svg>
          PrairieShingleWorks.com
        </li>
      </ul>
    </div>
  </section>

  <section class="card card-back" aria-label="Business card, brand side">
    <div class="back-brand">
      <span class="brand-square"></span>
      <span class="brand-name">BRENT Roofing &amp; Siding</span>
    </div>
    <p class="back-est">Est. 1991</p>
  </section>

</main>
</body>
</html>
```